Ledgerwise Forge - WordPress Theme & Logo

Design a logo and Wordpress website design for Ledgerwise Forge. Ledgerwise Forge provides cryptocurrency development services to clients who need a team to create & continue developing a new cryptocurrency or who want to replace their current cryptocurrency development team. more details in the attached document.
Updates

Target Market(s)

Entrepreneurs who are building a business / platform that makes use of an underlying cryptocurrency.

Logo Text

LF or Ledgerwise Forge

Coding

Coded - Design and coding required

Font styles to use
Sans Serif

Requirements
Must have
• Professional logo, complete coded Wordpress theme for all pages, containing all specified links and buttons
Nice to have
• It would be nice if the buttons that are meant to integrate with Dealtrail contain the necessary code for that. I can provide any necessary Dealtrail details from my account.
Should not have
• Slow loading time

```html
<!DOCTYPE html>
<html lang="en">
<head>
<meta charset="utf-8">
<title>Ledgerwise Forge</title>
<link rel="stylesheet" href="https://fonts.googleapis.com/css2?family=Rubik:wght@400;500;600&family=Saira:wght@500&display=swap">
<style>
:root{
  --navy:#0a1f6e;
  --navy-deep:#08185a;
  --blue:#1479d6;
  --blue-bright:#1a86e0;
  --ink:#2b2b2b;
  --muted:#555;
  --light:#f3f4f6;
  --white:#fff;
}
*{margin:0;padding:0;box-sizing:border-box}
html,body{width:1200px;height:3676px;overflow:hidden}
body{font-family:"Rubik",sans-serif;color:var(--ink);background:var(--white);position:relative}
.abs{position:absolute}
.brand{font-family:"Saira",sans-serif;font-weight:500;color:var(--white)}

/* hero */
.hero{left:0;top:0;width:1200px;height:814px;background:radial-gradient(ellipse at 70% 30%,#1b3c9a 0%,#10286f 55%,#0a1b55 100%)}
.hero-photo{left:60px;top:150px;width:480px;height:520px;border-radius:50%;background:radial-gradient(circle at 45% 40%,#d9a85a 0%,#a0712f 45%,rgba(20,40,100,0) 72%)}
.hero-edge{left:0;top:740px}
.logo-top{left:111px;top:44px;font-size:33px}
.nav{left:447px;top:57px;display:flex;gap:0;font-size:13px;font-weight:500;color:var(--white)}
.nav span{margin-right:41px}
.nav .active{color:#3a9bf0}
.hero-title{left:618px;top:262px;font-size:43px;font-weight:500;color:var(--white)}
.hero-sub{left:620px;top:332px;font-size:23px;font-weight:500;line-height:36px;color:var(--white)}
.btn{display:flex;align-items:center;justify-content:center;border-radius:30px;font-size:18px;font-weight:500;color:var(--white)}
.btn-pdf{left:622px;top:431px;width:240px;height:60px;background:var(--blue-bright)}
.btn-consult{left:869px;top:431px;width:285px;height:60px;border:2px solid var(--blue-bright)}

/* intro */
.intro{left:230px;top:866px;width:740px;text-align:center;font-size:16px;line-height:30px;color:#444}
.heading{left:0;width:1200px;text-align:center;font-size:33px;font-weight:500;color:var(--ink)}
.heading em{font-style:normal;color:var(--blue)}
.rule{width:46px;height:3px;background:var(--blue);left:577px}
.card{width:311px;height:291px;top:1122px;background:var(--white);border:1px solid #e3e8f0;box-shadow:0 2px 8px rgba(20,60,140,.12);text-align:center}
.card svg{position:absolute;left:50%;top:36px;transform:translateX(-50%)}
.card h3{position:absolute;top:144px;width:100%;font-size:24px;font-weight:500;color:var(--navy)}
.card p{position:absolute;top:190px;left:20px;right:20px;font-size:15.5px;line-height:24px;color:var(--muted)}

/* about */
.about-bg{left:0;top:1478px}
.about-photo{left:200px;top:1615px;width:366px;height:366px;border-radius:50%;background:linear-gradient(160deg,#d8dbe2 0%,#b9bec9 55%,#8d939f 100%);box-shadow:5px 6px 0 var(--navy)}
.about-title{left:628px;top:1628px;font-size:42px;font-weight:500;color:var(--white)}
.about-rule{left:634px;top:1689px;width:64px;height:3px;background:var(--white)}
.about-text{left:634px;top:1721px;width:400px;font-size:15px;line-height:25.7px;color:var(--white);text-align:justify}
.btn-more{left:638px;top:1906px;width:187px;height:59px;background:var(--navy)}

/* testimonials */
.avatar{width:176px;height:176px;border-radius:50%;top:2218px;background:radial-gradient(circle at 50% 45%,#b98a6c 0%,#6f5040 60%,#3d3431 100%)}
.t-name{width:330px;top:2417px;text-align:center;font-size:23px;font-weight:500;color:var(--blue)}
.t-text{width:290px;top:2457px;text-align:center;font-size:15px;line-height:26px;color:var(--muted)}

/* services */
.services-bg{left:0;top:2566px}
.tier{width:310px;height:468px;top:2803px;background:var(--blue-bright);color:var(--white)}
.tier-mid{top:2770px;background:var(--navy)}
.tier-img{height:224px;width:100%;background:linear-gradient(135deg,#0d1d4e 0%,#1f4f9a 55%,#0a1740 100%)}
.tier h3{text-align:center;font-size:21px;font-weight:500;line-height:30px;margin-top:20px}
.tier .desc{text-align:center;font-size:13.5px;line-height:25px;padding:8px 22px 0}
.tier ul{list-style:none;padding:12px 16px 0 16px}
.tier li{position:relative;padding-left:24px;font-size:13.5px;line-height:18px;margin-bottom:12px}
.tier li svg{position:absolute;left:0;top:3px}

/* footer */
.footer{left:0;top:3344px;width:1200px;height:332px;background:var(--navy-deep)}
.logo-foot{left:111px;top:3444px;font-size:27px}
.social{top:3494px;width:36px;height:36px;border:2px solid var(--white);border-radius:50%}
.foot-col{top:3412px;font-size:17px;line-height:32.4px;color:var(--white)}
.news-title{left:654px;top:3404px;font-size:20px;color:var(--white)}
.news-input{left:655px;top:3455px;width:297px;height:48px;background:var(--white);border-radius:4px 0 0 4px;font-size:13px;color:#333;padding:16px 15px}
.news-btn{left:952px;top:3455px;width:135px;height:48px;background:var(--blue-bright);border-radius:0 4px 4px 0;display:flex;align-items:center;justify-content:center;font-size:15px;font-weight:500;color:var(--white)}
.copyright{left:0;top:3628px;width:1200px;text-align:center;font-size:16px;color:var(--white)}
</style>
</head>
<body>

<section>
  <div class="abs hero"></div>
  <div class="abs hero-photo" role="img" aria-label="Close-up photo of a gold cryptocurrency coin on a circuit board"></div>
  <svg class="abs hero-edge" width="1200" height="74" viewBox="0 0 1200 74">
    <polygon points="0,70 770,31 1200,3 1200,74 0,74" fill="var(--blue-bright)"/>
    <polygon points="0,70 770,31 1200,74 0,74" fill="var(--white)"/>
  </svg>
  <div class="abs brand logo-top">Ledgerwise Forge</div>
  <nav class="abs nav">
    <span class="active">HOME</span><span>ABOUT</span><span>TESTIMONIALS</span><span>SERVICES</span><span>BOOK A CONSULTATION</span><span>BLOG</span>
  </nav>
  <h1 class="abs hero-title">Ledgerwise Forge</h1>
  <p class="abs hero-sub">Your own cryptocurrency. Secure, easy to use,<br>and built by an expert team</p>
  <div class="abs btn btn-pdf">Download a Free PDF</div>
  <div class="abs btn btn-consult">Schedule Free Consultation</div>
</section>

<section>
  <p class="abs intro">Ledgerwise Forge adds professionalism to cryptocurrency development. Our done-for-you service covers everything from development and IT operations to ongoing support. You have access to a full team, for less than the typical cost of a single developer.</p>
  <h2 class="abs heading" style="top:1020px">Why Choose <em>Ledgerwise Forge</em></h2>
  <div class="abs rule" style="top:1073px"></div>

  <div class="abs card" style="left:111px">
    <svg width="100" height="70" viewBox="0 0 100 70" fill="none" stroke="var(--blue)" stroke-width="3" stroke-linejoin="round">
      <path d="M50 2v10M32 6l4 9M68 6l-4 9M18 14l6 6M82 14l-6 6"/>
      <path d="M28 24h44l14 14-36 30-36-30z"/><path d="M14 38h72M40 24l-6 14 16 30 16-30-6-14"/>
    </svg>
    <h3>VALUE</h3>
    <p>A team of experts, regular updates, and fixed costs</p>
  </div>
  <div class="abs card" style="left:444px">
    <svg width="100" height="96" viewBox="0 0 100 96" fill="none" stroke="var(--blue)" stroke-width="3" stroke-linejoin="round" style="top:30px">
      <circle cx="50" cy="28" r="18"/><path d="M30 28a20 20 0 0 1 40 0M32 30v6M68 30v6"/>
      <path d="M20 90V66a14 14 0 0 1 14-14h32a14 14 0 0 1 14 14v24z"/>
      <rect x="36" y="62" width="28" height="18" rx="3"/><circle cx="50" cy="71" r="3"/><path d="M12 90h76"/>
    </svg>
    <h3>SUPPORT</h3>
    <p>Receive advice and other services, beyond development</p>
  </div>
  <div class="abs card" style="left:776px">
    <svg width="122" height="80" viewBox="0 0 122 80" fill="none" stroke="var(--blue)" stroke-width="3" stroke-linejoin="round">
      <path d="M4 20l18-14 14 18-18 14zM118 20l-18-14-14 18 18 14z"/>
      <path d="M36 24l14-6 12 4 12-6 12 8M34 36l22 26a6 6 0 0 0 9-8M50 52l12 14a6 6 0 0 0 9-8M62 48l12 12a6 6 0 0 0 9-8M86 40L62 22l-12 10a6 6 0 0 1-8-8"/>
    </svg>
    <h3>COMMITMENT</h3>
    <p>Enjoy regular updates and new features.</p>
  </div>
</section>

<section>
  <svg class="abs about-bg" width="1200" height="572" viewBox="0 0 1200 572">
    <polygon points="0,19 414,64 0,100" fill="var(--navy-deep)"/>
    <polygon points="0,100 1200,0 1200,572 0,572" fill="var(--blue-bright)"/>
  </svg>
  <div class="abs about-photo" role="img" aria-label="Portrait photo of a smiling team member in a server room"></div>
  <h2 class="abs about-title">Who we are</h2>
  <div class="abs about-rule"></div>
  <p class="abs about-text">In addition to creating and enhancing cryptocurrencies for clients, the Ledgerwise Forge team has been running the Norvel cryptocurrency since 2017. We prefer long-term relationships, enabling us to deliver the very highest quality and giving you peace of mind that you've got a professional and trustworthy team at your side.</p>
  <div class="abs btn btn-more">Read More</div>
</section>

<section>
  <h2 class="abs heading" style="top:2116px">Client <em>Testimonials</em></h2>
  <div class="abs rule" style="top:2169px"></div>

  <div class="abs avatar" style="left:185px" role="img" aria-label="Client portrait photo"></div>
  <div class="abs t-name" style="left:108px">Jhon Smith</div>
  <p class="abs t-text" style="left:128px">Sed ut perspiciatis unde omnis iste natus error sit voluptatem accusantium doloremque laudantium</p>

  <div class="abs avatar" style="left:512px" role="img" aria-label="Client portrait photo"></div>
  <div class="abs t-name" style="left:435px">Jhon Smith</div>
  <p class="abs t-text" style="left:455px">Sed ut perspiciatis unde omnis iste natus error sit voluptatem accusantium doloremque laudantium</p>

  <div class="abs avatar" style="left:840px" role="img" aria-label="Client portrait photo"></div>
  <div class="abs t-name" style="left:763px">Jhon Smith</div>
  <p class="abs t-text" style="left:783px">Sed ut perspiciatis unde omnis iste natus error sit voluptatem accusantium doloremque laudantium</p>
</section>

<section>
  <svg class="abs services-bg" width="1200" height="778" viewBox="0 0 1200 778">
    <rect x="0" y="0" width="1200" height="778" fill="var(--light)"/>
    <polygon points="0,0 1200,0 1200,44 0,4" fill="var(--white)"/>
    <polygon points="850,68 1200,44 1200,106" fill="var(--blue-bright)"/>
  </svg>
  <h2 class="abs heading" style="top:2681px">Service <em>Tiers</em></h2>
  <div class="abs rule" style="top:2734px"></div>

  <div class="abs tier" style="left:111px">
    <div class="tier-img" role="img" aria-label="Photo of hands on a laptop with network graphics"></div>
    <h3>Blockchain<br>Creation &amp; Launch</h3>
    <p class="desc">Base fixed price for cryptocurrency development &amp; launch--would be customizable based on client equirements</p>
  </div>

  <div class="abs tier tier-mid" style="left:445px">
    <div class="tier-img" role="img" aria-label="Photo of a digital security interface"></div>
    <h3>Basic offering</h3>
    <ul>
      <li><svg width="12" height="10" viewBox="0 0 12 10"><path d="M1 5l3.5 3.5L11 1" fill="none" stroke="#fff" stroke-width="2.2"/></svg>Lower cost per month</li>
      <li><svg width="12" height="10" viewBox="0 0 12 10"><path d="M1 5l3.5 3.5L11 1" fill="none" stroke="#fff" stroke-width="2.2"/></svg>Slower release schedule</li>
      <li><svg width="12" height="10" viewBox="0 0 12 10"><path d="M1 5l3.5 3.5L11 1" fill="none" stroke="#fff" stroke-width="2.2"/></svg>Client assists with testing new releases</li>
      <li><svg width="12" height="10" viewBox="0 0 12 10"><path d="M1 5l3.5 3.5L11 1" fill="none" stroke="#fff" stroke-width="2.2"/></svg>Less input into future roadmap/features</li>
      <li><svg width="12" height="10" viewBox="0 0 12 10"><path d="M1 5l3.5 3.5L11 1" fill="none" stroke="#fff" stroke-width="2.2"/></svg>Limited support hours/priority</li>
    </ul>
  </div>

  <div class="abs tier" style="left:779px">
    <div class="tier-img" role="img" aria-label="Photo of glowing code and circuit lines"></div>
    <h3>Full service offering</h3>
    <ul>
      <li><svg width="12" height="10" viewBox="0 0 12 10"><path d="M1 5l3.5 3.5L11 1" fill="none" stroke="#fff" stroke-width="2.2"/></svg>Mid-range cost per month</li>
      <li><svg width="12" height="10" viewBox="0 0 12 10"><path d="M1 5l3.5 3.5L11 1" fill="none" stroke="#fff" stroke-width="2.2"/></svg>Releases every 1.5 - 2 months</li>
      <li><svg width="12" height="10" viewBox="0 0 12 10"><path d="M1 5l3.5 3.5L11 1" fill="none" stroke="#fff" stroke-width="2.2"/></svg>Client can help request/prioritize new features</li>
      <li><svg width="12" height="10" viewBox="0 0 12 10"><path d="M1 5l3.5 3.5L11 1" fill="none" stroke="#fff" stroke-width="2.2"/></svg>Full testing by my team prior to release</li>
    </ul>
  </div>
</section>

<footer>
  <div class="abs footer"></div>
  <div class="abs brand logo-foot">Ledgerwise Forge</div>
  <div class="abs social" style="left:122px" aria-label="Social profile"></div>
  <div class="abs social" style="left:165px" aria-label="Social profile"></div>
  <div class="abs social" style="left:207px" aria-label="Social profile"></div>
  <div class="abs social" style="left:250px" aria-label="Social profile"></div>
  <div class="abs social" style="left:293px" aria-label="Social profile"></div>
  <div class="abs foot-col" style="left:377px">Home<br>About<br>Feature<br>Pricing<br>Contact</div>
  <div class="abs foot-col" style="left:532px">Blog<br>Search<br>T&amp;Cs<br>Privacy<br>Commu</div>
  <div class="abs news-title">Get Our Newsletter</div>
  <div class="abs news-input">Enter Your Email :</div>
  <div class="abs news-btn">SUBSCRIBE</div>
  <div class="abs copyright">©2021 Ledgerwise Forge.All rights reserved.</div>
</footer>

</body>
</html>
```